Commercial and Residential Paint Contractor needs website

We need a website for our residential painting, multi-family painting and commercial painting company. We paint interior and exterior of houses, apartments and commercial buildings. I would like an about us page, residential page, multi family page, commercial page and contact us. Need keywords added to website for seo opitimazation. I like this website https://www.wallcraftcrew.com/

Target Market(s)

General Contractors and commercial property managers

Coding

Coded - Design and coding required

Number of Pages Required

5+ page

Font styles to use
Sans Serif

Requirements
Must have
• I need SEO keywords on pages

```html
<!DOCTYPE html>
<html lang="en">
<head>
<meta charset="utf-8">
<title>Crestline Painting – Residential, Multi-family &amp; Commercial Painting</title>
<meta name="description" content="Crestline Painting: residential painting, multi-family painting and commercial painting contractor for interior and exterior projects.">
<link href="https://fonts.googleapis.com/css2?family=Michroma&family=Lato:ital,wght@0,400;0,700;0,900;1,400&display=swap" rel="stylesheet">
<style>
:root{
  --red:#c61f2c;
  --red-dark:#9c1119;
  --navy:#1e4a8c;
  --ink:#111;
  --grey-band:#f1f1f1;
  --text:#333;
  --field:#1b1b1b;
  --white:#fff;
}
*{box-sizing:border-box;margin:0;padding:0}
html,body{width:1200px;height:3898px;overflow:hidden}
body{position:relative;font-family:"Lato",sans-serif;color:var(--text);background:var(--white)}
.abs{position:absolute}
.display{font-family:"Michroma",sans-serif;font-weight:400;letter-spacing:2px;color:var(--ink)}
.btn{position:absolute;display:flex;align-items:center;justify-content:center;gap:8px;border-radius:24px;font-weight:700;font-size:16px;color:var(--white);background:var(--red)}

/* header */
.brand{left:92px;top:22px;font-weight:900;font-size:34px;line-height:1;color:var(--navy);letter-spacing:1px}
.contact-chip{top:28px;display:flex;gap:10px}
.contact-chip small{display:block;font-size:12px;color:#444}
.contact-chip b{display:block;font-weight:400;color:var(--ink)}
.contact-chip svg{margin-top:2px}
.nav{left:0;top:98px;width:1200px;height:45px;background:var(--red);display:flex;align-items:center}
.nav a{position:absolute;color:var(--white);font-size:15px;text-decoration:none;text-transform:uppercase}

/* hero */
.hero{left:0;top:143px;width:1200px;height:630px;background:linear-gradient(90deg,#e6e4e0 0%,#b71e24 12%,#c42a2c 40%,#cfcdca 58%,#9d9b98 82%,#bdbab6 100%)}
.hero::after{content:"";position:absolute;left:0;bottom:0;width:100%;height:180px;background:linear-gradient(180deg,rgba(0,0,0,0),rgba(196,140,70,.55))}
.hero-title{left:0;top:395px;width:1200px;text-align:center;color:var(--white);font-size:58px;letter-spacing:4px;z-index:2}
.hero-btn{left:510px;top:493px;width:179px;height:53px;background:var(--navy);z-index:2;font-size:18px}
.dots{left:557px;top:631px;display:flex;gap:10px;z-index:2}
.dots i{width:13px;height:13px;background:var(--white);border-radius:2px}
.dots i:first-child{background:var(--red)}

/* welcome */
.welcome{left:0;top:835px;width:1200px;text-align:center;font-size:40px}
.welcome span{color:var(--red)}
.service{width:331px}
.service .ph{width:331px;height:226px}
.service p{margin-top:12px;text-align:center;font-size:22px;color:var(--ink)}

/* about */
.about{left:0;top:1253px;width:1200px;height:461px;background:linear-gradient(110deg,var(--red-dark) 0%,#b0141d 45%,#a5121a 100%);text-align:center;color:var(--white)}
.about h2{color:var(--white);font-size:42px;margin-top:82px}
.about p{width:890px;margin:26px auto 0;font-size:16px;line-height:29.5px}
.about .btn{left:517px;top:324px;width:167px;height:45px;background:var(--white);color:var(--red);font-weight:400}

/* what we do */
.wwd-title{left:89px;top:1795px;font-size:40px}
.wwd-text{left:89px;top:1855px;width:369px;font-size:16px;line-height:30.5px;text-align:justify}
.tile{width:278px;height:191px}
.tile span{position:absolute;left:14px;bottom:10px;color:var(--white);font-weight:700;font-size:20px}

/* testimonials */
.testi{left:0;top:2286px;width:1200px;height:540px;background:var(--grey-band)}
.testi h2{position:absolute;left:0;top:85px;width:1200px;text-align:center;font-size:40px}
.card{top:203px;width:327px;height:247px;background:var(--white);box-shadow:0 2px 8px rgba(0,0,0,.08);text-align:center}
.avatar{position:absolute;left:109px;top:-57px;width:110px;height:110px;border-radius:50%;border:6px solid var(--white);background:linear-gradient(160deg,#d9c2b0,#6b4f3e)}
.card h3{margin-top:76px;font-size:17px;font-weight:400;color:var(--ink)}
.card p{margin:20px 22px 0;font-size:12.5px;font-style:italic;line-height:24px;color:#666}
.arrow{top:2595px}

/* gallery */
.gallery-title{left:0;top:2912px;width:1200px;text-align:center;font-size:40px}
.gph{top:2975px;width:227px;height:224px}

/* footer */
.footer{left:0;top:3320px;width:1200px;height:578px;background:#000;color:var(--white)}
.f-item{left:92px;display:flex;gap:22px;font-size:16px;line-height:27px}
.f-item svg{flex:none;margin-top:6px}
.field{background:var(--field);color:#ddd;font-size:15px;padding:12px 14px}
.copy{left:0;top:3858px;width:1200px;text-align:center;font-size:13px;color:#ccc}
</style>
</head>
<body>

<!-- Header -->
<div class="abs brand">CRESTLINE<br>PAINTING</div>
<div class="abs contact-chip" style="left:628px">
  <svg width="20" height="20" viewBox="0 0 20 20" fill="none" stroke="#c61f2c" stroke-width="1.5"><path d="M2 8l8-5 8 5v9H2z"/><path d="M2 8l8 5 8-5"/></svg>
  <div><small>Email Us :</small><b style="font-size:17px">hello@crestlinepainting.com</b></div>
</div>
<div class="abs contact-chip" style="left:912px">
  <svg width="20" height="20" viewBox="0 0 20 20" fill="none" stroke="#c61f2c" stroke-width="1.5"><path d="M5 2l3 4-2 2c1 3 3 5 6 6l2-2 4 3-2 3C8 17 3 12 2 4z"/></svg>
  <div><small>Call Us :</small><b style="font-size:22px">555-014-2290</b></div>
</div>

<nav class="abs nav">
  <a style="left:118px">Home</a>
  <a style="left:241px">About</a>
  <a style="left:378px">Residential Painting</a>
  <a style="left:629px">Commercial Painting</a>
  <a style="left:887px">Blog</a>
  <a style="left:1009px">Contact</a>
</nav>

<!-- Hero -->
<div class="abs hero" role="img" aria-label="Room with half-painted red wall, white doors and a wooden ladder"></div>
<h1 class="abs display hero-title">CRESTLINE PAINTING</h1>
<div class="btn hero-btn">Get a Quote
  <svg width="16" height="16" viewBox="0 0 16 16"><circle cx="8" cy="8" r="7" fill="#fff"/><path d="M6 4.5L9.5 8 6 11.5" stroke="#1e4a8c" stroke-width="2" fill="none"/></svg>
</div>
<div class="abs dots"><i></i><i></i><i></i></div>

<!-- Welcome -->
<h2 class="abs display welcome">WELCOME TO <span>CRESTLINE PAINTING</span></h2>
<div class="abs service" style="left:89px;top:903px">
  <div class="ph" role="img" aria-label="Painter brushing a window frame" style="background:linear-gradient(135deg,#7a4a2a,#c9b8a4 60%,#e8e2da)"></div>
  <p>Residential Painting</p>
</div>
<div class="abs service" style="left:434px;top:903px">
  <div class="ph" role="img" aria-label="Painter on scaffolding painting a building facade" style="background:linear-gradient(160deg,#8fae5a,#e0ddd4 45%,#6d6d6d)"></div>
  <p>Multi-family Painting</p>
</div>
<div class="abs service" style="left:779px;top:903px">
  <div class="ph" role="img" aria-label="Painter holding a paint roller" style="background:linear-gradient(90deg,#1d2537 0%,#2b3550 40%,#e9e7e4 70%,#f4f3f1)"></div>
  <p>Commercial Painting</p>
</div>

<!-- About -->
<section class="abs about" role="img" aria-label="Red tinted living room with sofa and cactus plants">
  <h2 class="display">ABOUT US</h2>
  <p>Lorem ipsum dolor sit amet, consectetur adipiscing elit, sed do eiusmod tempor incididunt ut labore et dolore magna aliqua. Ut enim ad minim veniam, quis nostrud exercitation ullamco laboris nisi ut aliquip ex ea commodo consequat. Duis aute irure dolor in reprehenderit in voluptate velit esse cillum dolore eu fugiat nulla pariatur. Excepteur sint occaecat cupidatat non proident, sunt in culpa qui officia deserunt mollit anim id est laborum</p>
  <div class="btn">Read More</div>
</section>

<!-- What we do -->
<h2 class="abs display wwd-title">WHAT WE DO</h2>
<p class="abs wwd-text">Lorem ipsum dolor sit amet, consectetur adipiscing elit, sed do eiusmod tempor incididunt ut labore et dolore magna aliqua. Ut enim ad minim veniam, quis nostrud exercitation ullamco laboris nisi ut aliquip ex ea commodo consequat. Duis aute irure dolor in reprehenderit in voluptate velit esse cillum dolore eu fugiat nulla pariatur. Excepteur sint occaecat cupidatat non proident, sunt in culpa qui officia deserunt mollit anim id est laborum</p>
<div class="btn" style="left:89px;top:2153px;width:168px;height:45px">Contact Us</div>

<div class="abs tile" style="left:539px;top:1800px;background:linear-gradient(120deg,#eee,#c7c2bc 50%,#3a5d80)" role="img" aria-label="Couple choosing paint colour swatches"><span>Interior House</span></div>
<div class="abs tile" style="left:832px;top:1800px;background:linear-gradient(180deg,#6f9bd0,#d8c8b0 55%,#8a7b6a)" role="img" aria-label="Two-storey house exterior being painted"><span>Exterior House</span></div>
<div class="abs tile" style="left:539px;top:2008px;background:linear-gradient(120deg,#3a74c0,#f07a2a 45%,#2bb3c8 75%,#e9d43a)" role="img" aria-label="Colourful painted apartment buildings"><span>Apartments</span></div>
<div class="abs tile" style="left:832px;top:2008px;background:linear-gradient(90deg,#3c4a5c,#a8adb4 55%,#dcdcdc)" role="img" aria-label="Workers painting a commercial building wall"><span>Commercial Buildings</span></div>

<!-- Testimonials -->
<section class="abs testi">
  <h2 class="display">TESTIMONIALS</h2>
  <div class="abs card" style="left:88px">
    <div class="avatar" role="img" aria-label="Client portrait"></div>
    <h3>Kara Lewis</h3>
    <p>Lorem ipsum dolor sit amet, consectetur adipiscing elit, sed do eiusmod tempor incididunt ut labore et dolore magna aliqua. Ut enim ad minim veniam, quis nostrud exercitation ullamco laboris</p>
  </div>
  <div class="abs card" style="left:436px">
    <div class="avatar" role="img" aria-label="Client portrait"></div>
    <h3>Jonah Reed</h3>
    <p>Lorem ipsum dolor sit amet, consectetur adipiscing elit, sed do eiusmod tempor incididunt ut labore et dolore magna aliqua. Ut enim ad minim veniam, quis nostrud exercitation ullamco laboris</p>
  </div>
  <div class="abs card" style="left:784px">
    <div class="avatar" role="img" aria-label="Client portrait"></div>
    <h3>Henry Hale</h3>
    <p>Lorem ipsum dolor sit amet, consectetur adipiscing elit, sed do eiusmod tempor incididunt ut labore et dolore magna aliqua. Ut enim ad minim veniam, quis nostrud exercitation ullamco laboris</p>
  </div>
</section>
<svg class="abs arrow" style="left:14px" width="38" height="66" viewBox="0 0 38 66"><path d="M34 3L5 33l29 30" stroke="#888" stroke-width="5" fill="none"/></svg>
<svg class="abs arrow" style="left:1148px" width="38" height="66" viewBox="0 0 38 66"><path d="M4 3l29 30L4 63" stroke="#888" stroke-width="5" fill="none"/></svg>

<!-- Gallery -->
<h2 class="abs display gallery-title">GALLERY</h2>
<div class="abs gph" style="left:138px;background:linear-gradient(135deg,#e9e6e0,#2c3f6a 55%,#d6c93a)" role="img" aria-label="Painter in yellow suit rolling a wall"></div>
<div class="abs gph" style="left:371px;background:linear-gradient(90deg,#3e78b8,#b8a6d8 60%,#e8e4ec)" role="img" aria-label="Freshly painted room with paint cans"></div>
<div class="abs gph" style="left:604px;background:linear-gradient(90deg,#f2f2f0,#cfcfcf 45%,#2d2d2d 60%,#3a3a3a)" role="img" aria-label="Workers on a lift painting a facade"></div>
<div class="abs gph" style="left:837px;background:linear-gradient(160deg,#2b5aa8,#6f92c8 50%,#c7d2de)" role="img" aria-label="Rope painters on a high-rise building"></div>
<div class="btn" style="left:517px;top:3220px;width:167px;height:45px">View All</div>

<!-- Footer -->
<footer class="abs footer"></footer>
<h2 class="abs display" style="left:92px;top:3443px;color:#fff;font-size:36px">ADDRESS</h2>
<div class="abs f-item" style="top:3517px">
  <svg width="14" height="18" viewBox="0 0 14 18"><path d="M7 0a7 7 0 00-7 7c0 5 7 11 7 11s7-6 7-11a7 7 0 00-7-7zm0 10a3 3 0 110-6 3 3 0 010 6z" fill="#fff"/></svg>
  <span style="color:#fff">PO Box 4410<br>Harbor Point, TX 70010</span>
</div>
<div class="abs f-item" style="top:3576px">
  <svg width="14" height="14" viewBox="0 0 20 20"><path d="M5 1l4 5-3 2c1 3 3 5 6 6l2-3 5 4-3 4C8 18 2 12 1 4z" fill="#fff"/></svg>
  <span style="color:#fff">(555)014-7781</span>
</div>
<div class="abs f-item" style="top:3607px">
  <svg width="16" height="12" viewBox="0 0 16 12"><rect width="16" height="12" rx="1" fill="#fff"/><path d="M0 1l8 6 8-6" stroke="#000" stroke-width="1.5" fill="none"/></svg>
  <span style="color:#fff">hello@crestlinepainting.com</span>
</div>
<div class="abs" style="left:136px;top:3656px;display:flex;gap:16px">
  <svg width="16" height="16"><rect width="16" height="16" rx="3" fill="none" stroke="#fff" stroke-width="2"/></svg>
  <svg width="16" height="16"><circle cx="8" cy="8" r="7" fill="none" stroke="#fff" stroke-width="2"/></svg>
  <svg width="16" height="16"><rect x="1" y="1" width="14" height="14" rx="4" fill="none" stroke="#fff" stroke-width="2"/><circle cx="8" cy="8" r="3" fill="none" stroke="#fff" stroke-width="2"/></svg>
</div>

<h2 class="abs display" style="left:599px;top:3441px;color:#fff;font-size:36px">CONTACT US</h2>
<div class="abs field" style="left:599px;top:3506px;width:247px;height:45px">First Name</div>
<div class="abs field" style="left:862px;top:3506px;width:247px;height:45px">Last Name</div>
<div class="abs field" style="left:599px;top:3569px;width:247px;height:46px">Email</div>
<div class="abs field" style="left:862px;top:3569px;width:247px;height:46px">Phone No</div>
<div class="abs field" style="left:599px;top:3634px;width:510px;height:90px">Message</div>
<div class="btn" style="left:599px;top:3740px;width:165px;height:46px">Submit</div>

<p class="abs copy">Copyrights © 2020, Crestline Painting. All rights reserved.</p>

</body>
</html>
```